Web Site Design and Business Card design for Recruiting Company

There are three major tasks in this project:
1) I need to re-design my newly created website www.talvoro.net using the same logo but creating a totally different recruiting template that will apply better for a recruitment site. I want to use the elements of the Talvoro Network logo (which is the road junction) and red, black and gray colors throughout the website. I need someone to both design and launch the site...
2) I would also like to design a double sided business card using the same logo/colors and elements as described above
3) I would also like to have a small thumbnail logo created. As our large logo cannot be previewed easily on the Pelmwork or on Google Chrome tab images

The design should be contemporary, minimalist and slick

```html
<!DOCTYPE html>
<html lang="en">
<head>
<meta charset="utf-8">
<title>Talvoro Network – Recruiting</title>
<link href="https://fonts.googleapis.com/css2?family=Montserrat:wght@400;500;600;700&family=Lato:wght@400;700&display=swap" rel="stylesheet">
<style>
:root{
  --red:#d7121b;
  --ink:#111111;
  --text:#555555;
  --muted:#777777;
  --navy:#0d1f38;
  --navy-deep:#07152a;
  --footer:#101a27;
  --band:#f2f2f2;
  --white:#ffffff;
}
*{box-sizing:border-box;margin:0;padding:0}
html,body{width:1200px;height:3773px;overflow:hidden}
body{font-family:'Lato',sans-serif;color:var(--text);background:var(--white);position:relative}
.section{position:absolute;left:0;width:1200px}
.abs{position:absolute}
.heading{font-family:'Montserrat',sans-serif;font-weight:600;color:var(--ink);text-transform:uppercase}
.rule{position:absolute;height:4px;background:var(--red);width:65px}

/* header */
.header{top:0;height:130px;background:var(--white)}
.brand{left:114px;top:40px;font-family:'Montserrat',sans-serif;font-weight:600;font-size:22px;color:var(--ink);display:flex;align-items:center;gap:10px}
.brand-mark{width:14px;height:14px;background:var(--red)}
.call-label{left:678px;top:31px;font-family:'Montserrat',sans-serif;font-weight:600;font-size:15px;color:var(--ink)}
.call-icon{left:813px;top:12px;width:44px;height:44px;border-radius:50%;background:var(--red)}
.call-number{left:882px;top:20px;font-family:'Montserrat',sans-serif;font-weight:700;font-size:22px;color:var(--ink);letter-spacing:1px}
.nav a{position:absolute;top:87px;font-family:'Montserrat',sans-serif;font-weight:700;font-size:14px;color:var(--ink);text-decoration:none}
.nav a.active{color:var(--red)}
.nav .underline{left:486px;top:120px;width:52px;height:4px;background:var(--red)}
.post-job{left:960px;top:72px;width:127px;height:41px;background:var(--red);color:var(--white);font-family:'Montserrat',sans-serif;font-weight:700;font-size:14px;display:flex;align-items:center;justify-content:center}

/* hero */
.hero{top:130px;height:583px;background:linear-gradient(180deg,#7fa6b8 0%,#3f6a82 45%,#1c3550 75%,#2b3440 100%)}
.hero-panel{left:212px;top:91px;width:773px;height:358px;background:rgba(120,130,140,.55)}
.hero-title{left:0;width:1200px;top:145px;text-align:center;font-family:'Montserrat',sans-serif;font-weight:600;font-size:45px;color:var(--white);letter-spacing:1px}
.hero-sub{left:0;width:1200px;top:210px;text-align:center;font-family:'Montserrat',sans-serif;font-size:15.5px;line-height:31px;color:var(--white)}
.select{top:293px;height:41px;width:322px;background:var(--white);font-family:'Montserrat',sans-serif;font-size:14px;color:#666;padding:12px 17px;display:flex;justify-content:space-between}
.search-btn{left:544px;top:353px;width:111px;height:41px;background:var(--red);color:var(--white);font-family:'Montserrat',sans-serif;font-size:15px;display:flex;align-items:center;justify-content:center;gap:7px}
.slide-arrow{top:265px;width:60px;height:60px;border-radius:50%;background:rgba(255,255,255,.3)}

/* welcome */
.welcome{top:713px;height:545px}
.welcome-title{left:0;width:1200px;top:88px;text-align:center;font-size:34px}
.welcome-text{left:150px;width:900px;top:170px;text-align:center;font-size:14px;line-height:28.5px;color:var(--muted)}
.feature{top:312px;width:270px;text-align:center}
.feature-icon{width:100px;height:100px;margin:0 auto;border-radius:8px;background:#f6dcdd}
.feature-label{margin-top:20px;font-family:'Montserrat',sans-serif;font-weight:600;font-size:19px;color:var(--ink)}

/* jobs */
.jobs{top:1258px;height:600px;background:linear-gradient(135deg,#1b2f4c 0%,var(--navy) 45%,var(--navy-deep) 100%)}
.jobs-photo{left:0;top:120px;width:110px;height:260px;background:linear-gradient(90deg,#c89f86,#7a5a48);border-radius:0 60px 60px 0;opacity:.8}
.jobs-title{top:74px;font-size:32px;color:var(--white)}
.job-card{left:111px;width:488px;height:104px;background:var(--white)}
.job-icon{left:19px;top:15px;width:74px;height:74px;border-radius:50%;background:#b8b8b8}
.job-text{left:120px;top:16px;width:320px;font-family:'Montserrat',sans-serif;font-size:11.5px;line-height:28px;color:var(--ink)}
.job-type{left:120px;top:70px;font-family:'Montserrat',sans-serif;font-size:11.5px;color:var(--red)}
.job-more{left:303px;top:70px;font-family:'Montserrat',sans-serif;font-size:11.5px;color:var(--red)}
.pager{top:520px;width:30px;height:30px;border-radius:50%;background:#c9c9c9}
.latest-text{left:658px;top:147px;width:430px;font-size:14.5px;line-height:28.3px;color:var(--white);text-align:justify}
.meta{font-size:14.5px;color:var(--white)}
.meta span{color:var(--red)}
.view-all{left:661px;top:434px;width:115px;height:41px;background:var(--red);color:var(--white);font-family:'Montserrat',sans-serif;font-weight:700;font-size:15px;display:flex;align-items:center;justify-content:center;gap:5px}

/* services */
.services{top:1858px;height:499px}
.services-title{left:0;width:1200px;top:46px;text-align:center;font-size:34px}
.service-box{top:143px;width:110px;height:109px;border:1px dashed var(--red);padding:14px}
.service-box div{width:100%;height:100%;background:#f6dcdd}
.service-arrow{top:197px}
.service-name{top:263px;width:300px;font-family:'Montserrat',sans-serif;font-weight:600;font-size:19px;line-height:28px;color:var(--ink);text-transform:uppercase}
.service-list{top:337px;list-style:none;font-family:'Montserrat',sans-serif;font-size:15px;line-height:28.5px;color:#666}
.service-list li{display:flex;align-items:center;gap:7px}
.dot{width:12px;height:12px;border-radius:50%;border:2px solid var(--red);position:relative}
.dot::after{content:"";position:absolute;left:2px;top:2px;width:4px;height:4px;border-radius:50%;background:var(--red)}

/* cta */
.cta{top:2357px;height:126px;background:var(--band)}
.cta-text{left:129px;top:52px;font-family:'Montserrat',sans-serif;font-weight:700;font-size:20px;color:#222;letter-spacing:.5px}
.cta-btn{left:788px;top:38px;width:301px;height:56px;background:var(--red);color:var(--white);font-family:'Montserrat',sans-serif;font-weight:700;font-size:16px;display:flex;align-items:center;justify-content:center;letter-spacing:.5px}

/* blog */
.blog{top:2483px;height:711px;background:linear-gradient(180deg,#4e5d70 0%,#6a7687 50%,#4a5566 100%)}
.blog-title{left:0;width:1200px;top:83px;text-align:center;font-size:34px;color:var(--white)}
.blog-sub{left:170px;width:860px;top:168px;text-align:center;font-family:'Montserrat',sans-serif;font-size:13.5px;line-height:27px;color:var(--white)}
.post{top:254px;width:299px;height:405px;background:var(--white)}
.post-photo{left:3px;top:3px;width:293px;height:190px}
.post-date{left:19px;top:223px;width:60px;height:57px;background:var(--red);color:var(--white);font-family:'Montserrat',sans-serif;font-weight:600;text-align:center;line-height:1}
.post-date b{display:block;font-size:15px;padding-top:10px}
.post-date i{display:block;font-style:normal;font-size:25px;padding-top:2px}
.post-title{left:90px;top:224px;font-family:'Montserrat',sans-serif;font-weight:500;font-size:19px;line-height:25.5px;color:var(--ink)}
.post-text{left:19px;top:302px;width:270px;font-family:'Lato',sans-serif;font-size:12.2px;line-height:24px;color:#333}

/* footer */
.footer{top:3194px;height:579px;background:var(--footer)}
.sub-title{left:0;width:1200px;top:83px;text-align:center;font-family:'Montserrat',sans-serif;font-weight:700;font-size:20px;color:var(--white);letter-spacing:.5px}
.sub-input{left:384px;top:149px;width:297px;height:41px;background:var(--white);font-family:'Montserrat',sans-serif;font-size:13px;color:#555;padding:13px 27px}
.sub-btn{left:694px;top:149px;width:134px;height:41px;background:var(--red);color:var(--white);font-family:'Montserrat',sans-serif;font-size:15px;display:flex;align-items:center;justify-content:center}
.sub-rule{left:112px;top:221px;width:977px;height:1px;background:rgba(255,255,255,.12)}
.col-title{top:250px;font-family:'Montserrat',sans-serif;font-weight:700;font-size:17px;color:var(--white)}
.col-list{top:292px;list-style:none;font-family:'Montserrat',sans-serif;font-size:15px;line-height:31px;color:var(--white)}
.chev{color:var(--white);font-size:12px;margin-right:10px}
.contact-row{font-family:'Montserrat',sans-serif;font-size:15px;line-height:31px;color:var(--white)}
.social{left:879px;display:flex;align-items:center;gap:20px;font-family:'Montserrat',sans-serif;font-size:18px;color:var(--white)}
.social-dot{width:49px;height:49px;border-radius:50%;background:var(--red)}
.copyright{left:0;width:1200px;top:543px;text-align:center;font-family:'Montserrat',sans-serif;font-size:15px;color:var(--white)}
</style>
</head>
<body>

<header class="section header">
  <div class="abs brand"><span class="brand-mark"></span>Talvoro Network</div>
  <div class="abs call-label">Call us Today</div>
  <div class="abs call-icon">
    <svg width="44" height="44" viewBox="0 0 44 44"><path d="M16 13c1.5-1 3-1 3.6.5l1.6 3.7c.4 1 0 2-.8 2.5l-1.5 1c.9 2.3 2.7 4.2 5 5.2l1.1-1.5c.6-.8 1.6-1.1 2.5-.7l3.7 1.7c1.4.6 1.4 2.2.4 3.6-1.4 2-3.8 2.6-6.2 1.6-4.8-2-8.5-5.8-10.4-10.6-.9-2.4-.4-4.6 1-6z" fill="#fff"/></svg>
  </div>
  <div class="abs call-number">+1-555-014-2290</div>
  <nav class="nav">
    <a class="active" style="left:486px">HOME</a>
    <a style="left:585px">ABOUT US</a>
    <a style="left:713px">SERVICES</a>
    <a style="left:838px">CONTACT US</a>
    <div class="abs underline"></div>
  </nav>
  <div class="abs post-job">POST A JOB</div>
</header>

<section class="section hero" role="img" aria-label="Night city skyline overlaid with a glowing network of connected lines">
  <div class="abs hero-panel"></div>
  <h1 class="abs hero-title">TALVORO NETWORK</h1>
  <p class="abs hero-sub">Sed ut perspiciatis unde omnis iste natus error sit voluptatem<br>accusantium doloremque laudantium, totam rem</p>
  <div class="abs select" style="left:265px"><span>Job Title</span><span>&#8964;</span></div>
  <div class="abs select" style="left:608px"><span>Job Title</span><span>&#8964;</span></div>
  <div class="abs search-btn">
    <svg width="14" height="14" viewBox="0 0 14 14"><circle cx="6" cy="6" r="4.3" fill="none" stroke="#fff" stroke-width="2"/><path d="M9 9l4 4" stroke="#fff" stroke-width="2.2"/></svg>Search
  </div>
  <div class="abs slide-arrow" style="left:21px"><svg width="60" height="60"><path d="M34 20l-10 10 10 10" fill="none" stroke="#fff" stroke-width="3"/></svg></div>
  <div class="abs slide-arrow" style="left:1115px"><svg width="60" height="60"><path d="M26 20l10 10-10 10" fill="none" stroke="#fff" stroke-width="3"/></svg></div>
</section>

<section class="section welcome">
  <h2 class="abs heading welcome-title">Welcome</h2>
  <div class="rule" style="left:567px;top:139px"></div>
  <p class="abs welcome-text">Sed ut perspiciatis unde omnis iste natus error sit voluptatem accusantium doloremque laudantium, totam rem aperiam, eaque ipsa quae ab illo inventore veritatis et quasi architecto beatae vitae dicta sunt explicabo. Nemo enim ipsam voluptatem quia voluptas sit aspernatur aut odit aut fugit, sed quia consequuntur magni dolores eos qui ratione voluptatem sequi nesciunt. Neque porro quisquam est, qui dolorem ipsum quia dolor sit amet, consectetur, adipisci velit, sed quia non numquam</p>
  <div class="abs feature" style="left:190px"><div class="feature-icon" role="img" aria-label="Line icon of two advisors in conversation"></div><div class="feature-label">Perspiciatis unde</div></div>
  <div class="abs feature" style="left:460px"><div class="feature-icon" role="img" aria-label="Line icon of a hand selecting a candidate"></div><div class="feature-label">Perspiciatis unde</div></div>
  <div class="abs feature" style="left:730px"><div class="feature-icon" role="img" aria-label="Line icon of a team joined by a handshake"></div><div class="feature-label">Perspiciatis unde</div></div>
</section>

<section class="section jobs" role="img" aria-label="Dark blue backdrop with a hand touching a screen of people icons">
  <div class="abs jobs-photo"></div>
  <h2 class="abs heading jobs-title" style="left:111px">Recent Job</h2>
  <div class="abs job-card" style="top:156px"><div class="abs job-icon"></div><p class="abs job-text">Sed ut perspiciatis unde omnis iste natus error sit voluptatem accusantium dolor</p><span class="abs job-type">Full Time</span><span class="abs job-more">View More Details</span></div>
  <div class="abs job-card" style="top:276px"><div class="abs job-icon"></div><p class="abs job-text">Sed ut perspiciatis unde omnis iste natus error sit voluptatem accusantium dolor</p><span class="abs job-type">Full Time</span><span class="abs job-more">View More Details</span></div>
  <div class="abs job-card" style="top:396px"><div class="abs job-icon"></div><p class="abs job-text">Sed ut perspiciatis unde omnis iste natus error sit voluptatem accusantium dolor</p><span class="abs job-type">Full Time</span><span class="abs job-more">View More Details</span></div>
  <div class="abs pager" style="left:531px"><svg width="30" height="30"><path d="M17 10l-5 5 5 5" fill="none" stroke="#333" stroke-width="2"/></svg></div>
  <div class="abs pager" style="left:569px"><svg width="30" height="30"><path d="M13 10l5 5-5 5" fill="none" stroke="#333" stroke-width="2"/></svg></div>

  <h2 class="abs heading jobs-title" style="left:655px">Latest Job Positions</h2>
  <div class="rule" style="left:658px;top:127px"></div>
  <p class="abs latest-text">Sed ut perspiciatis unde omnis iste natus error sit voluptatem accusantium doloremque laudantium, totam rem aperiam, eaque ipsa quae ab illo inventore veritatis et quasi architecto beatae vitae dicta sunt explicabo. Nemo enim ipsam voluptatem quia voluptas sit aspernatur aut odit aut fugit, sed quia consequuntur magni dolores eos qui ratione voluptatem sequi nesciunt. Neque porro quisquam est, qui dolorem</p>
  <div class="abs meta" style="left:658px;top:358px"><span>Perspiciatis :</span>&nbsp; Accusantium</div>
  <div class="abs meta" style="left:870px;top:358px"><span>Perspiciatis :</span>&nbsp; Doloremque</div>
  <div class="abs meta" style="left:658px;top:394px"><span>Perspiciatis :</span>&nbsp; Doloremque</div>
  <div class="abs meta" style="left:870px;top:394px"><span>Perspiciatis :</span>&nbsp; Accusantium</div>
  <div class="abs view-all">VIEW ALL <svg width="13" height="13"><circle cx="6.5" cy="6.5" r="6.5" fill="#fff"/><path d="M5 3.5l3 3-3 3" fill="none" stroke="#d7121b" stroke-width="2"/></svg></div>
</section>

<section class="section services">
  <h2 class="abs heading services-title">Our Services</h2>
  <div class="rule" style="left:567px;top:101px"></div>
  <div class="abs service-box" style="left:186px"><div role="img" aria-label="Line icon of a document under a magnifier"></div></div>
  <div class="abs service-box" style="left:511px"><div role="img" aria-label="Line icon of two people linked by a signal"></div></div>
  <div class="abs service-box" style="left:836px"><div role="img" aria-label="Line icon of a calculator and invoice"></div></div>
  <svg class="abs service-arrow" style="left:298px" width="211" height="14"><line x1="0" y1="7" x2="200" y2="7" stroke="#d7121b" stroke-width="2" stroke-dasharray="2 3"/><path d="M100 1l28 6-28 6z" fill="#d7121b"/></svg>
  <svg class="abs service-arrow" style="left:623px" width="211" height="14"><line x1="0" y1="7" x2="200" y2="7" stroke="#d7121b" stroke-width="2" stroke-dasharray="2 3"/><path d="M100 1l28 6-28 6z" fill="#d7121b"/></svg>
  <div class="abs service-name" style="left:186px">Information<br>Technology (IT)</div>
  <div class="abs service-name" style="left:510px">Telecommunications</div>
  <div class="abs service-name" style="left:834px">Accounting &amp;<br>Finance</div>
  <ul class="abs service-list" style="left:188px"><li><i class="dot"></i>Project Management</li><li><i class="dot"></i>Web and Application</li><li><i class="dot"></i>Network Administration</li></ul>
  <ul class="abs service-list" style="left:512px"><li><i class="dot"></i>Project Management</li><li><i class="dot"></i>Construction Management</li><li><i class="dot"></i>Site Acquisition</li></ul>
  <ul class="abs service-list" style="left:836px"><li><i class="dot"></i>Financial Planning</li><li><i class="dot"></i>Financial Management</li><li><i class="dot"></i>Certified Public Accounting</li></ul>
</section>

<section class="section cta">
  <div class="abs cta-text">FIND THE JOB OF YOUR DREAM IN A COUPLE OF CLICKS!</div>
  <div class="abs cta-btn">VIEW ALL JOB POSITION</div>
</section>

<section class="section blog" role="img" aria-label="Grey-blue backdrop with a faint web of connected points">
  <h2 class="abs heading blog-title">Latest Blog</h2>
  <div class="rule" style="left:567px;top:133px"></div>
  <p class="abs blog-sub">Sed ut perspiciatis unde omnis iste natus error sit voluptatem accusantium doloremque laudantium, totam rem aperiam,<br>eaque ipsa quae ab illo inventore veritatis et quasi architecto beatae vitae dicta</p>

  <article class="abs post" style="left:113px">
    <div class="abs post-photo" role="img" aria-label="Photo of a businesswoman in an interview" style="background:linear-gradient(135deg,#e8e6e2,#b9a898 60%,#4a4a4a)"></div>
    <div class="abs post-date"><b>FEB</b><i>05</i></div>
    <h3 class="abs post-title">Lorem ipsumotmet<br>consectetur iisin.</h3>
    <p class="abs post-text">Lorem ipsum dolor sit amet,rdiscing elit, seo eiusmod tempocnt ut labore et dolore malid minim veniam,uis nostrud exre</p>
  </article>
  <article class="abs post" style="left:451px">
    <div class="abs post-photo" role="img" aria-label="Photo of three colleagues at a meeting table" style="background:linear-gradient(135deg,#b7b5b0,#6f6a66 55%,#2e2e30)"></div>
    <div class="abs post-date"><b>FEB</b><i>05</i></div>
    <h3 class="abs post-title">Lorem ipsumotmet<br>consectetur iisin.</h3>
    <p class="abs post-text">Lorem ipsum dolor sit amet,rdiscing elit, seo eiusmod tempocnt ut labore et dolore malid minim veniam,uis nostrud exre</p>
  </article>
  <article class="abs post" style="left:790px">
    <div class="abs post-photo" role="img" aria-label="Photo of a smiling businessman in an office" style="background:linear-gradient(135deg,#5a6a80,#8a8f98 50%,#d9dde2)"></div>
    <div class="abs post-date"><b>FEB</b><i>05</i></div>
    <h3 class="abs post-title">Lorem ipsumotmet<br>consectetur iisin.</h3>
    <p class="abs post-text">Lorem ipsum dolor sit amet,rdiscing elit, seo eiusmod tempocnt ut labore et dolore malid minim veniam,uis nostrud exre</p>
  </article>
</section>

<footer class="section footer">
  <div class="abs sub-title">SUBSCRIBE FOR THE NEWSLETTER</div>
  <div class="abs sub-input">Email Address</div>
  <div class="abs sub-btn">SUBSCRIBE</div>
  <div class="abs sub-rule"></div>

  <div class="abs col-title" style="left:112px">INFORMATION</div>
  <ul class="abs col-list" style="left:112px">
    <li><span class="chev">&raquo;</span>Home</li>
    <li><span class="chev">&raquo;</span>Other Services</li>
    <li><span class="chev">&raquo;</span>About Us</li>
    <li><span class="chev">&raquo;</span>Contact</li>
    <li><span class="chev">&raquo;</span>Privacy</li>
    <li><span class="chev">&raquo;</span>Terms Conditions</li>
  </ul>

  <div class="abs col-title" style="left:334px">CONTACT US</div>
  <svg class="abs" style="left:334px;top:300px" width="12" height="16"><path d="M6 0a6 6 0 0 1 6 6c0 4-6 10-6 10S0 10 0 6a6 6 0 0 1 6-6z" fill="#fff"/><circle cx="6" cy="6" r="2.2" fill="#101a27"/></svg>
  <div class="abs contact-row" style="left:360px;top:292px">Sed ut perspiciatis unde<br>omnis iste natus</div>
  <svg class="abs" style="left:330px;top:383px" width="16" height="16"><path d="M3 1c1-.6 2-.5 2.4.4l1 2.4c.3.7 0 1.3-.5 1.7l-1 .6c.6 1.5 1.8 2.8 3.3 3.4l.7-1c.4-.5 1-.7 1.6-.4l2.4 1.1c.9.4.9 1.4.2 2.3-1 1.3-2.5 1.7-4 1C5.9 11.2 3.5 8.7 2.3 5.6 1.7 4 2 2.6 3 1z" fill="#fff"/></svg>
  <div class="abs contact-row" style="left:360px;top:375px">+1-555-014-2290</div>
  <svg class="abs" style="left:330px;top:439px" width="16" height="12"><rect width="16" height="12" fill="#fff"/><path d="M0 0l8 6 8-6" fill="none" stroke="#101a27" stroke-width="1.5"/></svg>
  <div class="abs contact-row" style="left:364px;top:430px">info@talvoro.net</div>

  <div class="abs col-title" style="left:602px">OPEN TIME</div>
  <svg class="abs" style="left:601px;top:299px" width="15" height="15"><circle cx="7.5" cy="7.5" r="6.3" fill="none" stroke="#fff" stroke-width="1.8"/><path d="M7.5 4v4h3" fill="none" stroke="#fff" stroke-width="1.6"/></svg>
  <ul class="abs col-list" style="left:626px">
    <li>Mon:&nbsp; 10:00 AM – 6:00 PM</li>
    <li>Tue:&nbsp;&nbsp; 10:00 AM – 6:00 PM</li>
    <li>Wed:&nbsp; 10:00 AM – 6:00 PM</li>
    <li>Thu:&nbsp;&nbsp; 10:00 AM – 6:00 PM</li>
    <li>Fri:&nbsp;&nbsp;&nbsp;&nbsp; 10:00 AM – 4:00 PM</li>
    <li>Sat:&nbsp;&nbsp;&nbsp; 12:00 PM – 2:00 PM</li>
    <li>Sun:&nbsp;&nbsp;&nbsp; Closed</li>
  </ul>

  <div class="abs social" style="top:291px"><span class="social-dot"></span>Friendwall</div>
  <div class="abs social" style="top:350px"><span class="social-dot"></span>Chirply</div>
  <div class="abs social" style="top:409px"><span class="social-dot"></span>Snapgrid</div>

  <div class="abs copyright">&copy; Copyrights 2019 All Rights Reserved | Talvoro</div>
</footer>

</body>
</html>
```